Business Card for Industrial Distributor

We need a business card design for an industrial distributor. We sell machine parts for the manufacturing and oil industry. We would like the cards to look clean and modern but with a touch of industry.

Our colors are blue/white.

Please feel free to visit our website www.korvelpartsco.com

Target Market(s)

mexican manufacturers in the automobile/aerospace industry

Industry/Entity Type

Industrial

Colors
ffffff
0555a3

```html
<!DOCTYPE html>
<html lang="en">
<head>
<meta charset="utf-8">
<title>Korvel Business Cards</title>
<link href="https://fonts.googleapis.com/css2?family=Lato:wght@400;700;900&display=swap" rel="stylesheet">
<style>
  :root {
    --stage: #3c3c3d;
    --paper: #ffffff;
    --brand-blue: #0555a3;
    --deep-blue: #2a3a93;
    --light-blue: #2478bb;
    --ink-grey: #6f6f73;
  }
  * { margin: 0; padding: 0; box-sizing: border-box; }
  html, body { width: 1200px; height: 810px; overflow: hidden; }
  body {
    background: var(--stage);
    font-family: "Lato", sans-serif;
    position: relative;
  }
  .card {
    position: absolute;
    width: 540px;
    height: 309px;
    background: var(--paper);
    border-radius: 22px;
    overflow: hidden;
  }
  .card--logo { left: 50px; top: 70px; }
  .card--contact { left: 610px; top: 430px; }

  .brand-panel {
    position: absolute;
    background: linear-gradient(135deg, var(--light-blue) 0%, var(--brand-blue) 45%, var(--deep-blue) 100%);
  }
  .card--logo .brand-panel { left: 0; top: 0; width: 210px; height: 309px; }
  .card--contact .brand-panel { right: 0; top: 0; width: 190px; height: 170px; border-bottom-left-radius: 22px; }

  .wordmark {
    font-family: "Lato", sans-serif;
    font-weight: 900;
    color: var(--deep-blue);
    letter-spacing: 1px;
    line-height: 1;
  }
  .logo-lockup {
    position: absolute;
    left: 262px; top: 118px;
    display: flex; align-items: center; gap: 12px;
  }
  .logo-dot { width: 30px; height: 30px; border-radius: 50%; background: var(--brand-blue); }
  .logo-lockup .wordmark { font-size: 54px; }
  .logo-url {
    position: absolute;
    left: 340px; top: 190px;
    font-size: 13px; color: var(--ink-grey);
  }

  .card--contact .wordmark {
    position: absolute; left: 34px; top: 36px; font-size: 62px;
  }
  .person { position: absolute; left: 40px; top: 128px; }
  .person-name { font-size: 22px; font-weight: 700; color: var(--deep-blue); }
  .person-title { font-size: 13px; color: var(--ink-grey); margin-top: 2px; }
  .address {
    position: absolute; left: 40px; top: 186px;
    font-size: 13px; line-height: 1.35; color: var(--ink-grey);
    font-style: normal;
  }
  .contact-list {
    position: absolute; left: 40px; top: 226px;
    list-style: none; font-size: 12.5px; color: var(--ink-grey); line-height: 1.45;
  }
  .contact-list li { display: flex; align-items: center; gap: 7px; }
  .contact-list svg { width: 12px; height: 12px; fill: var(--deep-blue); flex: none; }
  .contact-list .link { color: var(--deep-blue); }
</style>
</head>
<body>

<section class="card card--logo">
  <div class="brand-panel" role="img" aria-label="Blue gradient brand decoration"></div>
  <div class="logo-lockup">
    <span class="logo-dot"></span>
    <span class="wordmark">Korvel</span>
  </div>
  <p class="logo-url">www.korvelpartsco.com</p>
</section>

<section class="card card--contact">
  <div class="brand-panel" role="img" aria-label="Blue gradient brand decoration"></div>
  <span class="wordmark">Korvel</span>
  <div class="person">
    <p class="person-name">Marco Reyes</p>
    <p class="person-title">President &amp; CEO</p>
  </div>
  <address class="address">
    4120 Harbor Mill Rd,<br>Laredo, TX 78041
  </address>
  <ul class="contact-list">
    <li>
      <svg viewBox="0 0 12 12"><path d="M3 1h2l1 3-1.5 1a6 6 0 0 0 2.5 2.5L8 6l3 1v2a1 1 0 0 1-1 1A9 9 0 0 1 2 2a1 1 0 0 1 1-1z"/></svg>
      (956) 555 - 0142
    </li>
    <li>
      <svg viewBox="0 0 12 12"><rect x="3" y="1" width="6" height="3"/><rect x="1" y="5" width="10" height="4" rx="1"/><rect x="3" y="8" width="6" height="3"/></svg>
      (956) 555 - 0187
    </li>
    <li>
      <svg viewBox="0 0 12 12"><path d="M1 3h10v7H1z M1 3l5 4 5-4" fill="none" stroke="currentColor" style="stroke:#2a3a93" stroke-width="1.2"/></svg>
      sales@korvelpartsco.com
    </li>
    <li>
      <svg viewBox="0 0 12 12"><circle cx="6" cy="6" r="5" fill="none" style="stroke:#2a3a93" stroke-width="1.2"/><path d="M1 6h10M6 1c-3 3-3 7 0 10M6 1c3 3 3 7 0 10" fill="none" style="stroke:#2a3a93" stroke-width="1"/></svg>
      <span>www.<span class="link">korvelpartsco.com</span></span>
    </li>
  </ul>
</section>

</body>
</html>
```